Valdane Companies Business Card Design

We need a new business card for our Private Equity Real Estate Development firm, “Valdane” and our EB-5 regional center “Thornmere Regional Center” on one card. We prefer a design that is simple, elegant, and represents the luxury products we design and build as well as the financial security and stability our successful history has produced. We are an industry leader in our field and 3rd generation family business that has evolved into an institutional quality investment platform. Considered design size is standard business card dimensions (3.5 x 2 inches with an additional 1/8 inch space for design elements or backgrounds that extend beyond the finished size of your piece.

Target Market(s)

• High net worth individuals
• Highly skilled technical workers and physicians in the US seeking investment-based immigration opportunities
• Sophisticated private equity investors
• Intermediary partners include domestic attorneys and investment brokers, as well as international agent networks
• US real estate developers

Industry/Entity Type

Finance

Contact Information for Business Card

(Providing placeholder info for personal information, please design for longer character spaces, longer names and addresses etc..)
• Logo for Valdane
• Logo for Thornmere Regional Center
• Full name: Marcus Valdane
• Job title: CEO
• Email address: mvaldane@valdanecompanies.com
• Cell phone number: +1.555.314.2287
• Office number +1.555.628.4410
• Office address: Larkfield Court 5, 4817 Vista Orilla, Cedarvale, CA.
• Website: www.valdanecompanies.com

Font styles to use
Serif
Sans Serif

Colors
ec1f27
ffffff
000000

Requirements
Must have
• • Logo for Valdane
• • Logo for Thornmere Regional Center
• - Use rounded corners
• (See .ai file included for logos)
Nice to have
• • Simple, elegant design
• • Aesthetically compatible with our website design (www.valdanecompanies.com)
• • Color palette including but not limited to white, black, and red (as per logos)
Should not have
• - Not too much red color
• - Do not stack both logos on top of each other

```html
<!DOCTYPE html>
<html lang="en">
<head>
<meta charset="utf-8">
<title>Valdane Companies – Business Card</title>
<link rel="stylesheet" href="https://fonts.googleapis.com/css2?family=Cinzel:wght@600&family=Source+Sans+3:wght@400&display=swap">
<style>
  :root {
    --stage: #1a1a1a;
    --card: #0e0e0e;
    --ink: #ffffff;
    --rule: #4a4a4a;
    --serif: "Cinzel", "Trajan Pro", serif;
    --sans: "Source Sans 3", "Myriad Pro", sans-serif;
  }
  * { box-sizing: border-box; margin: 0; padding: 0; }
  html, body { width: 1200px; height: 900px; overflow: hidden; background: var(--stage); }
  .stage { position: relative; width: 1200px; height: 900px; }

  .card {
    position: absolute;
    left: 320px;
    width: 560px;
    height: 320px;
    background: var(--card);
    border-radius: 22px;
    box-shadow: 0 12px 30px rgba(0,0,0,.55);
    color: var(--ink);
  }
  .card--front { top: 100px; }
  .card--back  { top: 480px; }

  .brand {
    position: absolute;
    display: flex;
    align-items: center;
    gap: 14px;
    font-family: var(--serif);
    font-weight: 600;
    color: var(--ink);
    letter-spacing: .06em;
    text-transform: uppercase;
    white-space: nowrap;
  }
  .brand__square { width: 44px; height: 44px; background: var(--ink); flex: none; }
  .brand__name { line-height: 1.05; }

  .card--front .brand { left: 120px; top: 128px; font-size: 26px; }

  .card--back .brand { right: 40px; top: 40px; font-size: 26px; }
  .card--back .brand__square { width: 40px; height: 40px; }

  .rule-top {
    position: absolute; left: 250px; right: 40px; top: 108px;
    height: 1px; background: var(--rule);
  }

  .person { position: absolute; left: 40px; top: 186px; }
  .person__name {
    font-family: var(--serif); font-weight: 600;
    font-size: 20px; letter-spacing: .05em; text-transform: uppercase;
    white-space: nowrap;
  }
  .person__title { font-family: var(--sans); font-size: 14px; margin-top: 2px; }
  .person__address {
    font-family: var(--sans); font-size: 15px; line-height: 1.3;
    margin-top: 30px; color: var(--ink);
  }

  .contacts {
    position: absolute; right: 40px; top: 126px;
    list-style: none; text-align: right;
    font-family: var(--sans); font-size: 14px; line-height: 1.45;
  }
  .contacts li { display: flex; justify-content: flex-end; align-items: center; gap: 6px; white-space: nowrap; }
  .contacts svg { width: 12px; height: 12px; fill: var(--ink); flex: none; }
</style>
</head>
<body>
<main class="stage">

  <section class="card card--front" aria-label="Card front">
    <div class="brand">
      <span class="brand__square"></span>
      <span class="brand__name">Thornmere<br>Regional Center</span>
    </div>
  </section>

  <section class="card card--back" aria-label="Card back">
    <div class="brand">
      <span class="brand__square"></span>
      <span class="brand__name">Valdane Capital</span>
    </div>
    <div class="rule-top"></div>

    <div class="person">
      <p class="person__name">Marcus Valdane</p>
      <p class="person__title">CEO</p>
      <p class="person__address">Larkfield Court 5, 4817 Vista<br>Orilla, Cedarvale, CA</p>
    </div>

    <ul class="contacts">
      <li>+1.555.314.2287
        <svg viewBox="0 0 12 12" aria-hidden="true"><path d="M1 4c0-2 2-3 5-3s5 1 5 3l-2 1-1-1H4L3 5 1 4zm2 2h6l1 5H2l1-5zm3 1.2a1.4 1.4 0 1 0 0 2.8 1.4 1.4 0 0 0 0-2.8z"/></svg></li>
      <li>+1.555.628.4410
        <svg viewBox="0 0 12 12" aria-hidden="true"><path d="M3 0h6a1 1 0 0 1 1 1v10a1 1 0 0 1-1 1H3a1 1 0 0 1-1-1V1a1 1 0 0 1 1-1zm0 1.5v8h6v-8H3zm3 8.7a.6.6 0 1 0 0 1.2.6.6 0 0 0 0-1.2z"/></svg></li>
      <li>mvaldane@valdanecompanies.com
        <svg viewBox="0 0 12 12" aria-hidden="true"><path d="M0 2h12v8H0V2zm1 1v.3l5 3.4 5-3.4V3H1zm0 1.5V9h10V4.5L6 7.9 1 4.5z"/></svg></li>
      <li>www.valdanecompanies.com
        <svg viewBox="0 0 12 12" aria-hidden="true"><path d="M6 0a6 6 0 1 1 0 12A6 6 0 0 1 6 0zm-.8 8.6 4-4-.9-.9-3.1 3.1-1.4-1.4-.9.9 2.3 2.3z"/></svg></li>
    </ul>
  </section>

</main>
</body>
</html>
```